Specialised investor in e-mobility and energy wants business card design

We need a business card design that fits our existing corporate design. <The look and feel must be 'sharp'/'clean', dynamic, communicate momentum, professionalism etc (as one would imagine from a firm in the financial sector). We like the idea of a reverse-side of the card that includes the logo, and the name and contact details on the other. We expect the deliverable to be whatever format might be required to be able to get cards printed directly by a service such as kelmo press. Our website is www.zub.capital

```html
<!DOCTYPE html>
<html lang="en">
<head>
<meta charset="UTF-8">
<title>Zub Capital – Business Card</title>
<link href="https://fonts.googleapis.com/css2?family=Montserrat:wght@300;400;500;700&display=swap" rel="stylesheet">
<style>
  :root{
    --stage:#2b2d31;
    --card:#1b1b1d;
    --card-edge:#111113;
    --green:#86b54a;
    --white:#ffffff;
    --muted:#d9d9d9;
  }
  *{margin:0;padding:0;box-sizing:border-box}
  html,body{width:1200px;height:952px;overflow:hidden}
  body{
    background:var(--stage);
    font-family:"Montserrat",sans-serif;
    display:flex;flex-direction:column;align-items:center;justify-content:center;gap:64px;
  }
  .card{
    position:relative;width:580px;height:332px;background:var(--card);
    overflow:hidden;box-shadow:0 18px 40px rgba(0,0,0,.45);
  }
  /* wordmark */
  .wordmark{position:absolute;display:flex;align-items:center;gap:12px;color:var(--white);font-weight:400;letter-spacing:.5px;white-space:nowrap}
  .wordmark .mark{width:14px;height:14px;background:var(--green)}
  .front .wordmark{left:150px;top:40px;font-size:38px}
  .back .wordmark{left:50%;top:104px;transform:translateX(-50%);font-size:52px}

  /* front */
  .contact-band{position:absolute;left:0;top:0;width:580px;height:332px}
  .contact-list{position:absolute;left:26px;top:146px;list-style:none;display:flex;flex-direction:column;gap:9px}
  .contact-list li{display:flex;align-items:center;gap:10px;color:var(--white);font-size:15px;font-weight:400;white-space:nowrap}
  .contact-list .icon{width:20px;height:20px;background:var(--card);display:flex;align-items:center;justify-content:center;flex:none}
  .person{position:absolute;right:62px;bottom:46px;text-align:right}
  .person .name{font-size:25px;color:var(--white);font-weight:300;letter-spacing:1px;white-space:nowrap}
  .person .name strong{color:var(--green);font-weight:700}
  .person .role{font-size:15px;color:var(--white);font-weight:400;margin-top:2px}
  .accent-square{position:absolute;right:0;bottom:44px;width:46px;height:46px;background:var(--green)}

  /* back */
  .web-rule{position:absolute;left:0;right:0;top:236px;display:flex;align-items:center;gap:14px}
  .web-rule .line{flex:1;height:1px;background:var(--green)}
  .web-rule .url{font-size:13px;letter-spacing:3px;color:var(--muted);font-weight:400}
  .web-rule .url span{color:var(--green)}
</style>
</head>
<body>

  <section class="card front" aria-label="Business card front">
    <svg class="contact-band" viewBox="0 0 580 332" aria-hidden="true">
      <path d="M0 132 H240 Q280 168 316 196 L258 292 H0 Z" fill="var(--green)"/>
      <path d="M210 160 Q268 168 316 196" fill="none" stroke="var(--card)" stroke-width="5"/>
    </svg>

    <div class="wordmark"><span class="mark"></span>Zub Capital</div>

    <ul class="contact-list">
      <li>
        <span class="icon"><svg width="12" height="12" viewBox="0 0 24 24"><path fill="#fff" d="M6.6 10.8a15 15 0 0 0 6.6 6.6l2.2-2.2c.3-.3.7-.4 1-.2 1.1.4 2.3.6 3.6.6.6 0 1 .4 1 1V20c0 .6-.4 1-1 1A17 17 0 0 1 3 4c0-.6.4-1 1-1h3.5c.6 0 1 .4 1 1 0 1.3.2 2.5.6 3.6.1.3 0 .7-.2 1z"/></svg></span>
        +41 79 555 0148
      </li>
      <li>
        <span class="icon"><svg width="12" height="12" viewBox="0 0 24 24"><rect x="2" y="5" width="20" height="14" fill="none" stroke="#fff" stroke-width="2"/><path d="M2 5l10 8 10-8M2 19l8-7M22 19l-8-7" fill="none" stroke="#fff" stroke-width="2"/></svg></span>
        lena@zub.capital
      </li>
      <li>
        <span class="icon"><svg width="12" height="12" viewBox="0 0 24 24"><path fill="#fff" d="M12 2a7 7 0 0 0-7 7c0 5 7 13 7 13s7-8 7-13a7 7 0 0 0-7-7zm0 9.5A2.5 2.5 0 1 1 12 6a2.5 2.5 0 0 1 0 5.5z"/></svg></span>
        Arlenbach, Vestland
      </li>
    </ul>

    <div class="person">
      <p class="name">LENA <strong>MARSH</strong></p>
      <p class="role">Manager</p>
    </div>
    <span class="accent-square"></span>
  </section>

  <section class="card back" aria-label="Business card back">
    <div class="wordmark"><span class="mark"></span>Zub Capital</div>
    <div class="web-rule">
      <span class="line"></span>
      <span class="url">www.<span>zub</span>.capital</span>
      <span class="line"></span>
    </div>
  </section>

</body>
</html>
```